Business Card Design for Vintage Jazz

I am a vintage jazz band leader in New York City. My groups play the music of the 1920s, 1930s and 1940s. My website is morvalquist.com for more info on what I do.

I am looking for a two sided business card design that has the look and feel of a really nice business card from the 1930s. I need to convey with the design that my work has that vintage kind of class and style, but also conveys that we are fun and entertaining.

Most importantly it should make a bold staement. If Hal Denbrook had a card, what would it have looked like? I want a card that I feel confident will make an impact and will let people know that my work is te the top that NYC has to offer in vintage jazz..

Note that I have only decided to avoid the "committed payment" option as I have not used this service before. Assuming that I get quality work I will select a design from those presented.

Target Market(s)

people who want to hire my band for events, media, and new fans of the band

Industry/Entity Type

Performing Art

Contact Information for Business Card

Definitely a matte finish, possibly a sort of old style of paper with that brown tint? definitely a thick card.

Requirements
Must have
• FRONT
• My name: Tobin Vashley
• What I do: Bandleader, Guitarist, Vocalist, Songwriter
• Contact Details: morvalquist.com tobin@morvalquist.com 646-555-0148
• BACK
• My Social Media Links:
• facebook.morvalquist.com
• twitter, instagram, linkedin: morvalquist
• I'm also including a photo image I would like to use. The photo's background is not needed, and to be honest isn't really desireable. Just looking to use the image of me.
Nice to have
• I'm attaching which could be used as is, omitted from the card, or altered maybe with text going around the outside of the circle or in some other way. It may need some clean up to the edges of the lettering as we only use it for the website thumbnail.
• If there's space I'd like to include the text "join our mailing list for a free song download: freesong.morvalquist.com" If not perhaps just "Download a Free Song at: freesong.morvalquist.com - something to this end.
Should not have
• anything cartoony. Don't think retro 90s's vision of the swing era, think actual swing era!
• anything modern. Got to look old school
• Try to avoid dark backgrounds. Since we often play in bars and clubs where it is dar, a d
• avoid script fonts.

```html
<!DOCTYPE html>
<html lang="en">
<head>
<meta charset="utf-8">
<title>Tobin Vashley – Business Card</title>
<link rel="stylesheet" href="https://fonts.googleapis.com/css2?family=Source+Sans+3:ital,wght@0,400;0,600;1,400;1,700&display=swap">
<style>
  :root {
    --backdrop: #4a4a4a;
    --card-light: #ffffff;
    --card-dark: #000000;
    --ink: #111111;
    --ink-soft: #555555;
    --rule-light: #cfcfcf;
    --on-dark: #ffffff;
    --photo-top: #3a3a3a;
    --photo-bottom: #1c1c1c;
  }
  html, body {
    margin: 0;
    padding: 0;
    width: 1105px;
    height: 1200px;
    overflow: hidden;
    background: var(--backdrop);
    font-family: "Source Sans 3", "Myriad Pro", sans-serif;
  }
  .canvas { position: relative; width: 1105px; height: 1200px; }
  .card { position: absolute; left: 196px; width: 720px; height: 412px; overflow: hidden; }
  .card--front { top: 145px; background: var(--card-light); color: var(--ink); }
  .card--back { top: 602px; background: var(--card-dark); color: var(--on-dark); }

  /* Front */
  .brand-mark {
    position: absolute; left: 55px; top: 110px; width: 220px; height: 186px;
    display: flex; align-items: center; justify-content: center;
    font-weight: 600; font-size: 30px; color: var(--ink); text-align: center; line-height: 1.1;
  }
  .front-divider {
    position: absolute; left: 330px; top: 101px; width: 1px; height: 204px;
    background: var(--rule-light);
  }
  .identity { position: absolute; left: 374px; top: 114px; }
  .identity__name { margin: 0; font-size: 25px; font-weight: 600; line-height: 1.15; }
  .identity__role { margin: 2px 0 0; font-size: 19.5px; line-height: 1.4; color: var(--ink-soft); }
  .contact-list { position: absolute; left: 374px; top: 211px; margin: 0; padding: 0; list-style: none; }
  .contact-list li {
    display: flex; align-items: center; gap: 10px;
    font-size: 18.5px; line-height: 28px; color: var(--ink-soft);
  }
  .contact-list svg { width: 16px; height: 16px; flex: none; }

  /* Back */
  .portrait {
    position: absolute; left: 381px; top: 19px; width: 293px; height: 288px;
    background: linear-gradient(180deg, var(--photo-top), var(--photo-bottom));
  }
  .back-identity { position: absolute; left: 43px; top: 204px; }
  .back-identity__name { margin: 0; font-size: 25px; font-weight: 600; line-height: 1.15; }
  .back-identity__role { margin: 2px 0 0; font-size: 19.5px; line-height: 1.35; }
  .back-rule {
    position: absolute; left: 40px; top: 305px; width: 642px; height: 1px;
    background: var(--on-dark);
  }
  .social { position: absolute; left: 40px; top: 320px; }
  .social__row { display: flex; align-items: center; gap: 5px; height: 30px; margin-bottom: 4px; font-size: 19px; }
  .social__dot { width: 25px; height: 25px; border-radius: 50%; background: var(--on-dark); flex: none; }
  .social__handle { margin-left: 4px; }
  .free-song { position: absolute; right: 38px; top: 322px; text-align: right; }
  .free-song__lead { margin: 0; font-size: 19px; font-style: italic; line-height: 1.3; }
  .free-song__url { margin: 0; font-size: 20px; font-style: italic; font-weight: 700; line-height: 1.3; }
</style>
</head>
<body>
<main class="canvas">

  <section class="card card--front" aria-label="Card front">
    <div class="brand-mark">Tobin<br>Vashley</div>
    <div class="front-divider"></div>
    <div class="identity">
      <h1 class="identity__name">Tobin Vashley</h1>
      <p class="identity__role">Bandleader, Guitarist<br>Vocalist, Songwriter</p>
    </div>
    <ul class="contact-list">
      <li>
        <svg viewBox="0 0 16 16" aria-hidden="true"><rect x="3.5" y="1" width="9" height="14" rx="1.5" fill="none" stroke="#111" stroke-width="1.8"/><rect x="7" y="12" width="2" height="1.4" fill="#111"/></svg>
        646-555-0148
      </li>
      <li>
        <svg viewBox="0 0 16 16" aria-hidden="true"><rect x="1" y="3.5" width="14" height="9.5" fill="#111"/><path d="M1.5 4 L8 9 L14.5 4" fill="none" stroke="#fff" stroke-width="1.2"/></svg>
        tobin@morvalquist.com
      </li>
      <li>
        <svg viewBox="0 0 16 16" aria-hidden="true"><circle cx="8" cy="8" r="7" fill="#111"/><path d="M1 8 H15 M8 1 C4.5 4 4.5 12 8 15 M8 1 C11.5 4 11.5 12 8 15" fill="none" stroke="#fff" stroke-width="1"/></svg>
        morvalquist.com
      </li>
    </ul>
  </section>

  <section class="card card--back" aria-label="Card back">
    <div class="portrait" role="img" aria-label="Photo of the bandleader in a striped blazer, tipping a straw boater hat"></div>
    <div class="back-identity">
      <h2 class="back-identity__name">Tobin Vashley</h2>
      <p class="back-identity__role">Bandleader, Guitarist<br>Vocalist, Songwriter</p>
    </div>
    <div class="back-rule"></div>
    <div class="social">
      <div class="social__row"><span class="social__dot"></span><span class="social__handle">morvalquist.com</span></div>
      <div class="social__row"><span class="social__dot"></span><span class="social__dot"></span><span class="social__dot"></span><span class="social__handle">morvalquist</span></div>
    </div>
    <div class="free-song">
      <p class="free-song__lead">Download a Free Song at:</p>
      <p class="free-song__url">freesong.morvalquist.com</p>
    </div>
  </section>

</main>
</body>
</html>
```